Velk Partners Building Business Cards

We need a business card that reflects our business as "Solar Experts" in San Diego. Browse our website www.velkpartners.example our License needs to be displayed as "CSLB# 3867140" our phone number is (619) 555-0187

Save thousands on your electric bills and increase the value of your home while helping to protect the environment. Our solar installation experts will help you design the system that's right for you, using only the highest quality equipment that will look great and give you ideal performance. Our goal is to make you energy independent, and get your electric bill to 0.

Paul Osterby
(619) 555-0187
paul@velkpartners.example

Target Market(s)

Home owners in san diego looking for solar

Industry/Entity Type

Solar Energy

Contact Information for Business Card

Paul Osterby
(619) 555-0187
paul@velkpartners.example

Font styles to use
Other font styles liked:
• Use our logo font

Requirements
Must have
• License needs to be displayed as "CSLB# 3867140" our phone number is (619) 555-0187
Nice to have
• Real images of rooftop home solar in san diego
Should not have
• our business address

```html
<!DOCTYPE html>
<html lang="en">
<head>
<meta charset="utf-8">
<title>Velk Partners Building – Business Card</title>
<link rel="stylesheet" href="https://fonts.googleapis.com/css2?family=Roboto:wght@400;500;700&display=swap">
<style>
  :root {
    --page-bg: #d8d3cc;
    --card-bg: #eef0f2;
    --navy: #223e7a;
    --navy-text: #1f3a78;
    --gold: #efa21e;
    --gold-light: #f6c25a;
    --white: #ffffff;
    --license: #c9c3b8;
  }
  html, body {
    margin: 0;
    width: 1200px;
    height: 1200px;
    overflow: hidden;
    background: var(--page-bg);
    font-family: "Roboto", Arial, sans-serif;
  }
  .card {
    position: absolute;
    left: 100px;
    top: 308px;
    width: 1000px;
    height: 584px;
    background: var(--card-bg);
    overflow: hidden;
    box-shadow: 0 10px 30px rgba(0,0,0,0.15);
  }
  .card-waves {
    position: absolute;
    inset: 0;
  }
  .person {
    position: absolute;
    left: 52px;
    top: 72px;
    color: var(--navy-text);
  }
  .person-name {
    margin: 0;
    font-size: 31px;
    font-weight: 700;
    letter-spacing: -0.2px;
  }
  .person-title {
    margin: 6px 0 0;
    font-size: 22px;
    font-weight: 400;
  }
  .company-name {
    position: absolute;
    right: 50px;
    top: 74px;
    margin: 0;
    font-size: 46px;
    font-weight: 500;
    color: var(--navy-text);
    letter-spacing: -0.5px;
  }
  .contact-list {
    position: absolute;
    left: 52px;
    top: 326px;
    margin: 0;
    padding: 0;
    list-style: none;
    color: var(--navy-text);
    font-size: 23px;
  }
  .contact-item {
    display: flex;
    align-items: center;
    height: 36px;
  }
  .contact-icon {
    width: 22px;
    height: 22px;
    margin-right: 24px;
    flex: none;
  }
  .web-accent { color: var(--gold); }
  .license {
    position: absolute;
    right: 50px;
    top: 494px;
    margin: 0;
    font-size: 23px;
    color: var(--license);
  }
</style>
</head>
<body>
  <div class="card">
    <svg class="card-waves" viewBox="0 0 1000 584" width="1000" height="584" aria-hidden="true">
      <path d="M0 540 C 250 600, 470 540, 640 430 C 780 345, 890 330, 1000 328 V584 H0 Z" fill="var(--navy)"/>
      <path d="M0 512 C 220 575, 440 545, 610 430 C 760 330, 880 312, 1000 310" fill="none" stroke="var(--white)" stroke-width="22"/>
      <path d="M0 492 C 210 555, 430 540, 600 420 C 760 310, 880 295, 1000 292" fill="none" stroke="var(--gold)" stroke-width="14"/>
      <path d="M90 486 C 250 530, 400 520, 520 460" fill="none" stroke="var(--gold-light)" stroke-width="4"/>
    </svg>

    <div class="person">
      <p class="person-name">Paul Osterby</p>
      <p class="person-title">Managing Director</p>
    </div>

    <p class="company-name">Velk Partners Building</p>

    <ul class="contact-list">
      <li class="contact-item">
        <svg class="contact-icon" viewBox="0 0 24 24" aria-hidden="true">
          <path d="M3 8 C3 4 21 4 21 8 L18 10 L16 7 H8 L6 10 Z" fill="var(--gold)"/>
          <rect x="5" y="11" width="14" height="10" rx="2" fill="var(--gold)"/>
          <circle cx="12" cy="16" r="2.5" fill="var(--card-bg)"/>
        </svg>
        <span>(619) 555-0187</span>
      </li>
      <li class="contact-item">
        <svg class="contact-icon" viewBox="0 0 24 24" aria-hidden="true">
          <circle cx="12" cy="12" r="10" fill="var(--gold)"/>
          <g fill="none" stroke="var(--card-bg)" stroke-width="1.5">
            <ellipse cx="12" cy="12" rx="4" ry="10"/>
            <line x1="2" y1="12" x2="22" y2="12"/>
            <line x1="12" y1="2" x2="12" y2="22"/>
          </g>
        </svg>
        <span>paul@velkpartners.example</span>
      </li>
      <li class="contact-item">
        <svg class="contact-icon" viewBox="0 0 24 24" aria-hidden="true">
          <rect x="2" y="5" width="20" height="14" fill="var(--gold)"/>
          <path d="M2 5 L12 13 L22 5" fill="none" stroke="var(--card-bg)" stroke-width="1.5"/>
        </svg>
        <span>www.<span class="web-accent">velkpartners</span>.example</span>
      </li>
    </ul>

    <p class="license">License: CSLB# 3867140</p>
  </div>
</body>
</html>
```